Harborline Auto LLC

Car Dealer Customer Service
Address: 2874 Cresthaven Road, Shelbyville, TN 37162
web: www.harborlineautoxq.net
email: harborlineautoxq@mailnest.example
Phone: (931) 555-0148
Phone: (629) 555-0173

```html
<!DOCTYPE html>
<html lang="en">
<head>
<meta charset="utf-8">
<title>Harborline Auto LLC – Business Card</title>
<link href="https://fonts.googleapis.com/css2?family=Oswald:wght@500&family=Montserrat:wght@500;800&family=Open+Sans:wght@400&display=swap" rel="stylesheet">
<style>
  :root {
    --brand-blue: #1d77a8;
    --brand-blue-light: #2a8fc8;
    --brand-gold: #ecb140;
    --card-white: #ffffff;
    --backdrop: #e9ecef;
  }
  * { box-sizing: border-box; margin: 0; padding: 0; }
  html, body {
    width: 1200px; height: 1015px; overflow: hidden;
    background: var(--backdrop);
  }
  .sheet {
    position: relative; width: 1200px; height: 1015px;
    display: flex; flex-direction: column; align-items: center;
    justify-content: center; gap: 25px;
  }
  .card {
    position: relative; width: 840px; height: 480px;
    background: var(--card-white);
    box-shadow: 0 6px 20px rgba(0,0,0,0.18);
    overflow: hidden;
  }
  .card-art { position: absolute; inset: 0; width: 100%; height: 100%; }

  .tagline {
    position: absolute; left: 52px; top: 92px;
    font-family: "Oswald", sans-serif; font-weight: 500;
    font-size: 40px; color: var(--card-white); letter-spacing: 0.3px;
  }
  .brand {
    position: absolute; display: flex; align-items: center; gap: 14px;
  }
  .brand-dot {
    width: 26px; height: 26px; border-radius: 50%;
    background: var(--brand-gold);
  }
  .brand-name {
    font-family: "Montserrat", sans-serif; font-weight: 800;
    font-size: 40px; line-height: 1.2; color: var(--brand-blue); letter-spacing: 1px;
    text-transform: uppercase; white-space: nowrap;
  }
  .card--front .brand { right: 44px; top: 330px; }
  .card--back .brand { left: 48px; top: 150px; }

  .person {
    position: absolute; right: 48px; top: 38px; text-align: right;
    font-family: "Montserrat", sans-serif;
  }
  .person-name {
    font-weight: 800; font-size: 26px; color: var(--brand-blue);
    text-transform: uppercase; letter-spacing: 0.5px;
  }
  .person-role { font-weight: 500; font-size: 20px; color: var(--brand-gold); }

  .contact {
    position: absolute; right: 40px; top: 262px; text-align: right;
    font-family: "Open Sans", sans-serif; font-size: 18px; line-height: 1.45;
    color: var(--card-white); list-style: none;
  }
  .contact li { display: flex; justify-content: flex-end; align-items: center; gap: 8px; }
  .contact .address { margin-bottom: 10px; }
  .contact svg { width: 16px; height: 16px; flex: none; }
</style>
</head>
<body>
<main class="sheet">

  <section class="card card--front" aria-label="Business card front">
    <svg class="card-art" viewBox="0 0 840 480" aria-hidden="true">
      <path d="M0,0 H840 V70 C700,55 620,90 540,170 C430,280 260,330 0,345 Z" fill="var(--brand-blue)"/>
      <path d="M0,351 C260,336 430,286 540,176 C620,96 700,61 840,76" fill="none" stroke="var(--card-white)" stroke-width="8"/>
      <path d="M0,359 C260,344 430,294 540,184 C620,104 700,69 840,84" fill="none" stroke="var(--brand-blue-light)" stroke-width="8"/>
      <path d="M250,368 C400,340 480,290 560,205 C640,125 720,95 840,100" fill="none" stroke="var(--brand-gold)" stroke-width="7"/>
    </svg>
    <p class="tagline">Car Dealer Customer Service</p>
    <div class="brand">
      <span class="brand-dot"></span>
      <span class="brand-name">Harborline Auto</span>
    </div>
  </section>

  <section class="card card--back" aria-label="Business card back">
    <svg class="card-art" viewBox="0 0 840 480" aria-hidden="true">
      <path d="M0,480 V420 C260,420 400,380 500,280 C590,190 680,160 840,160 V480 Z" fill="var(--brand-blue)"/>
      <path d="M0,414 C260,414 400,374 500,274 C590,184 680,154 840,154" fill="none" stroke="var(--card-white)" stroke-width="8"/>
      <path d="M0,406 C260,406 400,366 500,266 C590,176 680,146 840,146" fill="none" stroke="var(--brand-blue-light)" stroke-width="8"/>
      <path d="M0,392 C240,392 380,352 470,262 C510,222 540,205 580,190" fill="none" stroke="var(--brand-gold)" stroke-width="8"/>
    </svg>
    <div class="person">
      <p class="person-name">Dorian Vale</p>
      <p class="person-role">Managing Director</p>
    </div>
    <div class="brand">
      <span class="brand-dot"></span>
      <span class="brand-name">Harborline Auto</span>
    </div>
    <ul class="contact">
      <li class="address">2874 Cresthaven Road<br>Shelbyville, TN 37162</li>
      <li>(931) 555-0148
        <svg viewBox="0 0 16 16"><path d="M4 1 L7 4 L5 6 C6 8 8 10 10 11 L12 9 L15 12 L13 15 C7 15 1 9 1 3 Z" fill="var(--brand-gold)"/></svg></li>
      <li>(629) 555-0173
        <svg viewBox="0 0 16 16"><path d="M4 1 L7 4 L5 6 C6 8 8 10 10 11 L12 9 L15 12 L13 15 C7 15 1 9 1 3 Z" fill="var(--brand-gold)"/></svg></li>
      <li>www.harborlineautoxq.net
        <svg viewBox="0 0 16 16" fill="none" stroke="var(--brand-gold)" stroke-width="1.5"><circle cx="8" cy="8" r="6.5"/><path d="M1.5 8 H14.5 M8 1.5 C5 5 5 11 8 14.5 M8 1.5 C11 5 11 11 8 14.5"/></svg></li>
      <li>harborlineautoxq@mailnest.example
        <svg viewBox="0 0 16 16"><rect x="1" y="3" width="14" height="10" fill="var(--brand-gold)"/><path d="M1 3 L8 9 L15 3" fill="none" stroke="var(--brand-blue)" stroke-width="1.3"/></svg></li>
    </ul>
  </section>

</main>
</body>
</html>
```